International business needs business cards

Our company, DRV Ventures Inc. is in the business of supplying a range construction products with particular emphasis on CEMENT. We have developed our own brand - TORVAN SUPPLIES - with which to infiltrate the market. We are launching our brand of cement (TORVAN Type IS Cement) into the Caribbean which is unlike anything this market has ever seen. A monopoly has existed here for the past 60-odd years and the market has now opened to allow the importation of other brands and consumers are anxious and ready for change/improvement. We are very excited to be launching and want to make a great first impression. We will be conducting workshops and seminars (from government level to the hardware store owners) and we want our business card to give us the strong, confident introduction that we need.

Target Market(s)

construction; builders; engineers; home owners

Industry/Entity Type

Construction

Contact Information for Business Card

Marisol Depree
CEO
cell # 1 555 4180736
Ground floor,Lindell Plaza Suite 2734
George Town,Grand Cayman
Cayman Islands,KY1-4823
EMAIL: m.depree@drvventuresinc.example
web site drvventuresinc.example

COMPANY: skype info drv.ventures.example

second card
Yvette Brannock-Depree
CFO
CELL# 1 555 607 3941
George Town,Grand Cayman
Cayman Islands,KY1-4823
EMAIL: y.brannockdepree@drvventuresinc.example
website drvventuresinc.example

Requirements
Must have
• Business cards must display BOTH logos - DRV is the company and TORVAN is the brand.

```html
<!DOCTYPE html>
<html lang="en">
<head>
<meta charset="utf-8">
<title>DRV Ventures Inc. — Business Card</title>
<link rel="stylesheet" href="https://fonts.googleapis.com/css2?family=Source+Sans+3:wght@400;600;700;900&display=swap">
<style>
  :root {
    --backdrop: #e9e9ec;
    --maroon: #7a1416;
    --maroon-light: #861a1c;
    --maroon-text: #7b1518;
    --ink: #161616;
    --paper: #ffffff;
    --muted: #2a2a2a;
  }
  * { box-sizing: border-box; margin: 0; padding: 0; }
  html, body { width: 1200px; height: 864px; overflow: hidden; }
  body {
    background: var(--backdrop);
    font-family: "Source Sans 3", Arial, sans-serif;
    position: relative;
  }
  .card {
    position: absolute;
    width: 580px;
    height: 332px;
    border-radius: 3px;
    box-shadow: 0 6px 18px rgba(0,0,0,.18);
    overflow: hidden;
  }

  /* Front face */
  .card-front {
    left: 310px; top: 60px;
    background: var(--maroon);
  }
  .card-front .band {
    position: absolute; top: 0; bottom: 0;
    background: var(--maroon-light);
  }
  .card-front .band-left { left: 0; width: 70px; }
  .card-front .band-right { right: 0; width: 80px; }
  .front-wordmark {
    position: absolute; left: 0; right: 0; top: 92px;
    text-align: center; color: var(--paper);
    font-weight: 900; line-height: 1;
  }
  .front-wordmark .mark-name { font-size: 74px; letter-spacing: 1px; }
  .front-wordmark .mark-sub { font-size: 17px; letter-spacing: 1px; margin-top: 2px; }
  .brand-tile {
    position: absolute; left: 50%; top: 212px;
    width: 70px; height: 56px; margin-left: -35px;
    background: var(--paper);
    display: flex; align-items: center; justify-content: center;
    color: var(--maroon); font-weight: 700; font-size: 13px; letter-spacing: .5px;
  }

  /* Back face */
  .card-back {
    left: 250px; top: 440px;
    background: var(--paper);
  }
  .back-logo {
    position: absolute; left: 168px; top: 40px;
    display: flex; align-items: center; gap: 12px;
  }
  .back-logo .logo-square { width: 96px; height: 92px; background: var(--maroon); }
  .back-logo .logo-text { color: var(--ink); font-weight: 900; line-height: 1; }
  .back-logo .mark-name { font-size: 70px; letter-spacing: 1px; }
  .back-logo .mark-sub { font-size: 18px; letter-spacing: 1px; }

  .holder { position: absolute; left: 52px; top: 150px; }
  .holder-name { color: var(--maroon-text); font-size: 21px; font-weight: 700; }
  .holder-role { color: var(--muted); font-size: 13px; margin-top: -2px; }

  .address {
    position: absolute; left: 52px; top: 214px;
    font-size: 15px; line-height: 1.35; color: var(--ink);
  }
  .contacts {
    position: absolute; right: 28px; top: 244px;
    list-style: none; text-align: right;
    font-size: 15px; color: var(--ink);
  }
  .contacts li {
    display: flex; justify-content: flex-end; align-items: center;
    gap: 8px; line-height: 24px;
  }
  .contacts svg { width: 13px; height: 13px; fill: var(--maroon); }
</style>
</head>
<body>

  <section class="card card-front" aria-label="Card front">
    <div class="band band-left"></div>
    <div class="band band-right"></div>
    <div class="front-wordmark">
      <div class="mark-name">DRV</div>
      <div class="mark-sub">VENTURES INC.</div>
    </div>
    <div class="brand-tile">TORVAN</div>
  </section>

  <section class="card card-back" aria-label="Card back">
    <div class="back-logo">
      <div class="logo-square"></div>
      <div class="logo-text">
        <div class="mark-name">DRV</div>
        <div class="mark-sub">VENTURES INC.</div>
      </div>
    </div>

    <div class="holder">
      <div class="holder-name">Marisol Depree</div>
      <div class="holder-role">CEO</div>
    </div>

    <address class="address" style="font-style:normal">
      Ground floor, Lindell Plaza Suite 2734<br>
      George Town, Grand Cayman<br>
      Cayman Islands, KY1-4823
    </address>

    <ul class="contacts">
      <li>1 555 4180736
        <svg viewBox="0 0 16 16" aria-hidden="true"><path d="M3.6 1.5l2.3 2.6-1.3 1.8c.9 2 2.5 3.6 4.5 4.5l1.8-1.3 2.6 2.3-1.2 2.4C7.5 13.6 2.4 8.5 1.2 3.7z"/></svg>
      </li>
      <li>m.depree@drvventuresinc.example
        <svg viewBox="0 0 16 16" aria-hidden="true"><path d="M1 3h14v10H1z M2 4l6 5 6-5" fill="none" stroke="#7a1416" stroke-width="1.6"/></svg>
      </li>
      <li>www.drvventuresinc.example
        <svg viewBox="0 0 16 16" aria-hidden="true"><circle cx="8" cy="8" r="7"/><path d="M1 8h14M8 1c-3 3-3 11 0 14M8 1c3 3 3 11 0 14" fill="none" stroke="#fff" stroke-width="1"/></svg>
      </li>
    </ul>
  </section>

</body>
</html>
```